Home Security Company Business Card

Looking for a eye catching business card that is non traditional and stands out but yet still looks professional. It should include all the pertinent information such as name, title, address, telephone, e-mail, website address should definitely stand out and then finally the logo.

Target Market(s)

Residential and Commercial accounts mostly upscale accounts

Industry/Entity Type

Security

Contact Information for Business Card

Name
Title
Address
Office #
Cell #
E-mail
Website

Font styles to use
Serif
Sans Serif

Requirements
Must have
• Logo, two sided color configuration
Nice to have
• You decide
Should not have
• There really aren't any.

```html
<!DOCTYPE html>
<html lang="en">
<head>
<meta charset="utf-8">
<title>Ironvale Security – Business Card</title>
<link rel="stylesheet" href="https://fonts.googleapis.com/css2?family=Source+Sans+3:ital,wght@0,400;0,600;1,400&display=swap">
<style>
  :root {
    --backdrop: #3b3b3b;
    --paper: #fbfbfb;
    --crimson: #741000;
    --crimson-deep: #6a0e00;
    --gold: #d9a33a;
    --gold-light: #f0cf6c;
    --ink: #3a3a3a;
    --rule: #9a9a9a;
    --white: #ffffff;
  }
  * { margin: 0; padding: 0; box-sizing: border-box; }
  html, body {
    width: 1200px; height: 750px; overflow: hidden;
    background: var(--backdrop);
    font-family: "Source Sans 3", sans-serif;
  }
  .stage { position: relative; width: 1200px; height: 750px; }
  .card {
    position: absolute; top: 228px;
    width: 461px; height: 263px; overflow: hidden;
  }
  .card--front { left: 124px; background: var(--paper); }
  .card--back { left: 618px; background: var(--crimson); }

  .brand {
    position: absolute; right: 28px; top: 58px;
    display: flex; align-items: center; gap: 8px;
    color: var(--crimson); font-size: 21px; font-weight: 600;
    letter-spacing: 0.5px;
  }
  .brand__mark { width: 14px; height: 14px; background: var(--crimson); }

  .holder { position: absolute; left: 25px; top: 142px; }
  .holder__name { font-size: 19px; font-weight: 600; color: var(--crimson); line-height: 1; }
  .holder__title { font-size: 14px; color: var(--gold); line-height: 1; margin-top: 4px; }
  .rule {
    position: absolute; left: 102px; right: 29px; top: 175px;
    height: 1px; background: var(--rule);
  }

  .contacts { position: absolute; left: 24px; top: 188px; list-style: none; }
  .contacts li {
    display: flex; align-items: center; gap: 6px;
    height: 18px; font-size: 12px; color: var(--ink);
  }
  .contacts svg { width: 12px; height: 12px; fill: var(--crimson); }

  .address {
    position: absolute; right: 29px; top: 188px; text-align: right;
    font-style: normal; font-size: 12px; color: var(--ink); line-height: 18px;
  }

  .band { position: absolute; left: 0; bottom: 0; width: 461px; height: 9px; }

  .back-brand {
    position: absolute; left: 0; right: 0; top: 100px;
    display: flex; justify-content: center; align-items: center; gap: 10px;
    color: var(--gold-light); font-size: 28px; font-weight: 600; letter-spacing: 1px;
  }
  .back-brand__mark { width: 16px; height: 16px; background: var(--gold-light); }
  .back-web {
    position: absolute; left: 0; right: 0; top: 214px; text-align: center;
    color: var(--white); font-size: 12px; font-style: italic; letter-spacing: 4px;
  }
</style>
</head>
<body>
<main class="stage">
  <section class="card card--front" aria-label="Business card front">
    <div class="brand"><span class="brand__mark"></span>Ironvale Security</div>

    <div class="holder">
      <p class="holder__name">Daniel Harper</p>
      <p class="holder__title">CEO/Founder</p>
    </div>
    <div class="rule"></div>

    <ul class="contacts">
      <li>
        <svg viewBox="0 0 24 24" aria-hidden="true"><path d="M6.6 10.8a15.1 15.1 0 0 0 6.6 6.6l2.2-2.2a1 1 0 0 1 1-.25 11.4 11.4 0 0 0 3.6.57 1 1 0 0 1 1 1V20a1 1 0 0 1-1 1A17 17 0 0 1 3 4a1 1 0 0 1 1-1h3.5a1 1 0 0 1 1 1c0 1.25.2 2.45.57 3.57a1 1 0 0 1-.25 1z"/></svg>
        555 210 4876
      </li>
      <li>
        <svg viewBox="0 0 24 24" aria-hidden="true"><path d="M7 1h10a2 2 0 0 1 2 2v18a2 2 0 0 1-2 2H7a2 2 0 0 1-2-2V3a2 2 0 0 1 2-2zm0 3v14h10V4zm5 15.2a1.2 1.2 0 1 0 0 2.4 1.2 1.2 0 0 0 0-2.4z"/></svg>
        555 318 6042
      </li>
      <li>
        <svg viewBox="0 0 24 24" aria-hidden="true"><path d="M2 5h20v14H2zm2 2v.4l8 5 8-5V7zm0 2.8V17h16V9.8l-8 5z"/></svg>
        mail@ironvale.com
      </li>
    </ul>

    <address class="address">
      1420 Willow Crest Lane<br>
      Fairbanks, Alaska 99701<br>
      www.ironvale.com
    </address>

    <svg class="band" viewBox="0 0 461 9" preserveAspectRatio="none" aria-hidden="true">
      <defs>
        <linearGradient id="goldBand" x1="0" x2="1" y1="0" y2="0">
          <stop offset="0" stop-color="#b8822a"/>
          <stop offset="1" stop-color="#f0cf6c"/>
        </linearGradient>
      </defs>
      <rect x="0" y="0" width="461" height="9" fill="#741000"/>
      <polygon points="302,0 461,0 461,9 299,9" fill="url(#goldBand)"/>
      <polygon points="299,0 302,0 299,9 296,9" fill="#ffffff"/>
    </svg>
  </section>

  <section class="card card--back" aria-label="Business card back">
    <div class="back-brand"><span class="back-brand__mark"></span>Ironvale Security</div>
    <p class="back-web">www.ironvale.com</p>
  </section>
</main>
</body>
</html>
```